Merindola! Poster

I need a poster for an event to be staged in Gibraltar called Merindola!
Merindola! is a food festival and street party that celebrates GIbraltar's multicultural and colour community. The event has a tagline "Flavours of the Busy Kettle".
I am looking for a poster which captures the spirit of the event without being too obvious.
Updates

Because this event is rapidly approaching I would like to settle the design for the poster as soon as possible, so the earlier you post the better
thanks

I am trying to avoid a poster that looks too similar to last year's.
Red and White are Gibraltar's national colours and I would like to feature them in the design.
Merindola! the name needs to be in Clarendon! (bold) with tight character spacing

Target Market(s)

Target market are the people of Gibraltar - Gibraltar is a british colony in southern Spain, population 30,000 - Gibraltarians are of British, Spanish, Italian (Genoa), Portugese and Moroccan extraction. Gibraltar also has large Hindu, Jewish and Moroccan Communities.

Industry/Entity Type

Events

Requirements
Must have
• Initially I am looking for an A2 design - we will use the same design themes for the website and also base a 120cm x 90cm banner on the design.
• Must have t
• "BrightLanternShows.example" "Merindola!" , "Flavours of the Busy Kettle", Friday June 19th 2009, Tollbrook Square, Starts 21.00 hrs Finishes 0100 hrs, Free Entry, Everyone Welcome, Firework and Laser Display at 22.30 hrs
• My company logo, Bureau of Heritage Bloom Fair Logo
• Title must use Clarendon font
Nice to have
• Could be a photo or an illustration nothing that too obviously reflects the theme, doesn''t need to have all or anymore than one of the main Gibraltarian cultures
Should not have
• picture of the ROck of Gibaltar, Money, bad photography in particular bad food photography, just a picture of some food

```html
<!DOCTYPE html>
<html lang="en">
<head>
<meta charset="utf-8">
<title>Merindola! Poster</title>
<link rel="stylesheet" href="https://fonts.googleapis.com/css2?family=Ultra&family=Bevan&family=Archivo:wght@700;800&family=Roboto+Condensed:wght@400;700&display=block">
<style>
  :root {
    --paper: #ffffff;
    --red: #ef4135;
    --ink: #161616;
    --grey: #6e6e6e;
    --cream: #f3eed6;
    --night: #0d0d0f;
    --gold: #d8b24a;
  }
  * { margin: 0; padding: 0; box-sizing: border-box; }
  html, body { width: 1200px; height: 908px; overflow: hidden; background: var(--paper); }
  .poster { position: relative; width: 1200px; height: 908px; background: var(--paper); }

  .hero {
    position: absolute; left: 18px; top: 18px; width: 1164px; height: 648px;
    background:
      radial-gradient(circle at 50% 38%, var(--cream) 0 17%, #e2d6a6 19%, #cbbf94 24%, rgba(30,28,24,0.9) 34%, var(--night) 50%),
      var(--night);
  }
  .web-tab {
    position: absolute; left: 38px; top: 18px; width: 368px; height: 44px;
    background: var(--red); border-bottom-right-radius: 12px;
    color: var(--paper); font: 700 17px/44px "Archivo", sans-serif;
    letter-spacing: 3.2px; padding-left: 16px;
  }
  .entry {
    position: absolute; left: 922px; top: 556px; color: var(--paper);
    font: 700 24px/32px "Roboto Condensed", sans-serif;
  }
  .entry .free {
    color: var(--red); font-family: "Ultra", "Bevan", "Clarendon", "Rockwell", Georgia, serif;
    font-weight: 700; font-size: 27px; letter-spacing: -0.5px;
  }

  .title-band {
    position: absolute; left: 18px; top: 666px; width: 1164px; height: 98px;
    background: var(--red);
  }
  .title {
    position: absolute; left: 58px; top: 670px; color: var(--paper);
    font-family: "Ultra", "Bevan", "Clarendon", "Rockwell", Georgia, serif;
    font-weight: 700; font-size: 84px; line-height: 90px; letter-spacing: -2.5px;
    white-space: nowrap;
  }

  .event-type {
    position: absolute; left: 62px; top: 778px; color: var(--ink);
    font: 800 23px/30px "Archivo", sans-serif; letter-spacing: 2.4px;
  }
  .tagline {
    position: absolute; left: 310px; top: 776px; color: var(--ink);
    font: 700 28px/31px "Roboto Condensed", sans-serif; letter-spacing: 1.6px;
  }
  .divider { position: absolute; top: 774px; width: 2px; height: 66px; background: var(--red); }
  .divider.first { left: 298px; }
  .divider.second { left: 546px; top: 770px; height: 80px; }
  .details {
    position: absolute; left: 554px; top: 778px; color: var(--grey);
    font: 700 19px/28px "Roboto Condensed", sans-serif;
  }
  .display {
    position: absolute; left: 62px; top: 850px; color: var(--grey);
    font: 700 20px/26px "Roboto Condensed", sans-serif;
  }

  .partner {
    position: absolute; left: 872px; top: 790px; width: 116px; color: var(--ink);
    font: 700 15px/17px "Roboto Condensed", sans-serif;
  }
  .partner .mark { display: block; width: 18px; height: 18px; border-radius: 50%; background: var(--red); margin-bottom: 6px; }
  .promoter {
    position: absolute; left: 1016px; top: 832px; color: var(--ink);
    font: 700 14px/18px "Roboto Condensed", sans-serif; letter-spacing: 0.6px;
    display: flex; align-items: center; gap: 6px; white-space: nowrap;
  }
  .promoter .mark { width: 12px; height: 12px; background: var(--ink); }
</style>
</head>
<body>
<main class="poster">
  <div class="hero" role="img" aria-label="Overhead photo of a round banquet table set with gold charger plates, glasses and a flower centrepiece, surrounded by cream chair covers tied with gold bows on a dark floor"></div>
  <div class="web-tab">BrightLanternShows.example</div>
  <p class="entry"><span class="free">Free</span> Entry<br>Everyone Welcome</p>

  <div class="title-band"></div>
  <h1 class="title">Merindola!</h1>

  <p class="event-type">FOOD FESTIVAL<br>STREET PARTY</p>
  <span class="divider first"></span>
  <p class="tagline">Flavours of the<br>Busy Kettle</p>
  <span class="divider second"></span>
  <p class="details">Friday June 19th 2009<br>Tollbrook Square,<br>Starts 21.00 hrs Finishes 0100 hrs,</p>
  <p class="display">Firework and Laser Display at 22.30 hrs</p>

  <p class="partner"><span class="mark"></span>Bureau of Heritage Bloom Fair</p>
  <p class="promoter"><span class="mark"></span>BrightLantern Shows</p>
</main>
</body>
</html>
```